Consulting Company PowerPoint Template Design

We are looking for an updated PowerPoint template design or our 55 person energy consulting firm (K7) based in San Francisco (www.kseven-example.com). We would like two versions of the same PowerPoint template in a 16:9 and 4:3 format with our existing logo.

We have an existing color scheme and template and are seeking your help to polish/update the template design for wide format and create a flexible template that is easy to use with content from Excel and Word. Our current template, and a couple of examples that we like are attached.

Specific requests include:

• Dark background for slide title
• A narrow section header
• Maximizing white space for content
• A limited number of well designed Master template layouts to choose from
• A selection of title and section header slides that are not San Francisco specific with some variety to chose from ideally with a focus on energy or nature, graphics/visuals.

For examples of energy specific templates see:
https://www.brightslidehub.example/energy/powerpoint-templates/0.html

Requirements
Must have
• Must use our logo but open to other designs, fonts, and styles for the PowerPoint template.
• Please use our existing color scheme found in the attached Excel file.
• Also we would like the ability to easily copy and paste from our existing/original template to the new template. In other words we would like backward compatibility to apply the new template format to our old PowerPoints that use our existing template.

```html
<!DOCTYPE html>
<html lang="en">
<head>
<meta charset="utf-8">
<title>K7 Title Slide</title>
<link rel="stylesheet" href="https://fonts.googleapis.com/css2?family=Roboto+Condensed:wght@700&family=Titillium+Web:wght@600&display=swap">
<style>
  :root {
    --canvas-grey: #ececec;
    --canvas-grey-dark: #dedede;
    --hero-blue: #1b5d7f;
    --hero-blue-deep: #124a66;
    --hero-outline: #1f2a30;
    --brand-blue: #1d5d7e;
    --accent-gold: #cfb273;
    --white: #ffffff;
  }
  * { margin: 0; padding: 0; box-sizing: border-box; }
  html, body {
    width: 1200px;
    height: 900px;
    overflow: hidden;
    background: var(--canvas-grey);
  }
  .slide {
    position: relative;
    width: 1200px;
    height: 900px;
    overflow: hidden;
    background: radial-gradient(ellipse at 20% 30%, var(--canvas-grey-dark) 0%, var(--canvas-grey) 60%);
  }
  .hero-image {
    position: absolute;
    left: 327px;
    top: -2px;
    right: -2px;
    height: 579px;
    border: 2px solid var(--hero-outline);
    border-bottom-left-radius: 48px;
    background: linear-gradient(180deg, var(--hero-blue) 0%, #2a6a8a 45%, var(--hero-blue-deep) 100%);
  }
  .project-title {
    position: absolute;
    left: 327px;
    right: 0;
    top: 250px;
    text-align: center;
    font-family: "Roboto Condensed", "Arial Narrow", sans-serif;
    font-weight: 700;
    font-size: 57px;
    letter-spacing: 0.5px;
    color: var(--white);
  }
  .gold-block {
    position: absolute;
    left: 0;
    top: 551px;
    width: 395px;
    height: 349px;
    background: var(--accent-gold);
    border-top-right-radius: 62px;
  }
  .brand {
    position: absolute;
    left: 420px;
    right: 0;
    top: 636px;
    display: flex;
    flex-direction: column;
    align-items: center;
  }
  .brand-mark {
    width: 116px;
    height: 116px;
    border-radius: 50%;
    background: var(--brand-blue);
    border: 4px solid var(--canvas-grey);
    box-shadow: 0 0 0 2px #c9d4da;
  }
  .brand-name {
    margin-top: 22px;
    font-family: "Titillium Web", "Segoe UI", sans-serif;
    font-weight: 600;
    font-size: 41px;
    color: var(--brand-blue);
  }
</style>
</head>
<body>
  <main class="slide">
    <div class="hero-image" role="img" aria-label="Blue-toned photograph of wind turbines on a flat field under a cloudy sky"></div>
    <h1 class="project-title">PROJECT TITLE HERE</h1>
    <div class="gold-block"></div>
    <div class="brand">
      <div class="brand-mark"></div>
      <p class="brand-name">Keystone Power Economics</p>
    </div>
  </main>
</body>
</html>
```